UI/ UX Design for ERP Software

We need a new UX/UI interface for a ERP software for property managers. Our CMMS / ERP solution is made based on responsive design technologies and is coded in PHP.
The overall UX to be similar to Tev Ulna - easy navigation, intuitive menus.

Industry/Entity Type

Property Management

Number of Pages Required

5+ page

Requirements
Must have
• Round dock buttons
Consistent icons across the application
Enough Spacing between buttons/icons/ menu
Consistent Font
Nice to have
• We would like the UX to allow the users to use the application without /minimum training.
Should not have
• we don't want anything that is classic with respect to UX

```html
<!DOCTYPE html>
<html lang="en">
<head>
<meta charset="utf-8">
<title>Active Dashboard</title>
<link href="https://fonts.googleapis.com/css2?family=Roboto:wght@400;500&display=swap" rel="stylesheet">
<style>
:root{
  --page:#e9f5fc;
  --header:#eaf6fd;
  --ink-blue:#2a3fc7;
  --side:#2438c4;
  --white:#ffffff;
  --orange:#e88f4b;
  --green:#3cb828;
  --pink:#f23b6b;
  --blue-card:#1c63c4;
  --cyan:#0bbcf6;
  --indigo:#2a35c2;
  --violet:#41309b;
  --panel:#f4f8fc;
  --col-pink:#f5e4ec;
  --col-blue:#c4e0fb;
  --bar:#77b4f0;
  --grid:#6e6e6e;
  --legend:#58a1f7;
  --text-dark:#333;
}
*{margin:0;padding:0;box-sizing:border-box}
html,body{width:1200px;height:643px;overflow:hidden}
body{background:var(--page);font-family:'Roboto',Arial,sans-serif;position:relative}
.header{position:absolute;left:0;top:0;width:1200px;height:53px;background:var(--header);box-shadow:0 1px 3px rgba(0,0,0,.05)}
.header .home{position:absolute;left:31px;top:17px}
.header h1{position:absolute;left:64px;top:18px;font-size:14px;font-weight:400;color:var(--ink-blue)}

.sidebar{position:absolute;left:1031px;top:0;width:169px;height:643px;background:var(--side);border-radius:14px 0 0 14px}
.nav{list-style:none;position:absolute;left:0;top:5px;width:169px}
.nav li{height:28.7px;display:flex;align-items:center;color:var(--white);font-size:11px;position:relative;white-space:nowrap}
.nav li svg{position:absolute;left:10px;width:16px;height:16px;fill:var(--white)}
.nav li span{position:absolute;left:48px}
.nav li.active{background:var(--white);color:var(--side);width:143px;margin-left:-2px;border-radius:0 8px 8px 0}
.nav li.active svg{fill:var(--side);left:12px}
.nav li.active span{left:50px}

.pill{position:absolute;left:25px;width:164px;border-radius:12px;color:var(--white);font-size:11px;display:flex;align-items:center;justify-content:center;gap:6px}
.range{top:76px;height:31px;background:var(--orange)}
.dates{top:118px;height:39px;background:var(--green);font-size:10.5px}
.count{position:absolute;top:167px;height:64px;border-radius:14px;color:var(--white);text-align:center}
.count b{display:block;font-weight:400;font-size:15px;margin-top:12px}
.count small{display:flex;justify-content:center;align-items:center;gap:6px;font-size:10.5px;margin-top:6px}
.count.props{left:25px;width:77px;background:var(--pink)}
.count.tenants{left:112px;width:78px;background:var(--blue-card)}
.area{position:absolute;left:25px;width:164px;height:91px;border-radius:16px;color:var(--white);text-align:center}
.area b{display:block;font-weight:400;font-size:15.5px;margin-top:24px}
.area small{display:flex;justify-content:center;align-items:center;gap:6px;font-size:10.5px;margin-top:9px}
.area.total{top:241px;background:var(--cyan)}
.area.rented{top:343px;background:var(--indigo)}
.area.vacant{top:446px;background:var(--violet)}

.chart{position:absolute;left:213px;top:77px;width:793px;height:460px;background:var(--panel);border-radius:16px}
.chart svg{position:absolute;left:0;top:0}

.legend{position:absolute;left:25px;top:554px;width:981px;height:71px;background:var(--legend);border-radius:22px;color:var(--white);font-size:11px}
.legend .item{position:absolute;display:flex;align-items:center;gap:8px;white-space:nowrap}
.legend .dot{width:15px;height:15px;border-radius:50%;border:1px solid rgba(255,255,255,.9)}
</style>
</head>
<body>
<header class="header">
  <svg class="home" width="20" height="18" viewBox="0 0 20 18"><path d="M10 0 0 9h3v9h5v-6h4v6h5V9h3z" fill="#2a3fc7"/></svg>
  <h1>Active Dashboard</h1>
</header>

<div class="pill range">
  <svg width="12" height="12" viewBox="0 0 12 12"><circle cx="6" cy="6" r="6" fill="#fff"/><path d="M6 3v3l2 1.5" stroke="#e88f4b" stroke-width="1.3" fill="none"/></svg>
  Last 7 Days
  <svg width="10" height="8" viewBox="0 0 10 8"><path d="M0 0h10L5 8z" fill="#fff"/></svg>
</div>
<div class="pill dates">
  <svg width="13" height="12" viewBox="0 0 13 12"><rect x="0" y="1" width="13" height="11" fill="#fff"/><rect x="1.5" y="4" width="10" height="6.5" fill="#3cb828"/><rect x="2.5" y="5" width="2" height="1.5" fill="#fff"/><rect x="5.5" y="5" width="2" height="1.5" fill="#fff"/><rect x="8.5" y="5" width="2" height="1.5" fill="#fff"/><rect x="2.5" y="8" width="2" height="1.5" fill="#fff"/><rect x="5.5" y="8" width="2" height="1.5" fill="#fff"/></svg>
  27/12/2020 - 03/01/2021
  <svg width="10" height="8" viewBox="0 0 10 8"><path d="M0 0h10L5 8z" fill="#fff"/></svg>
</div>

<div class="count props"><b>3</b><small><svg width="11" height="13" viewBox="0 0 11 13"><path d="M5.5 0A5.5 5.5 0 0 0 0 5.5C0 9 5.5 13 5.5 13S11 9 11 5.5A5.5 5.5 0 0 0 5.5 0z" fill="#fff"/><circle cx="5.5" cy="5.5" r="2" fill="#f23b6b"/></svg>Propertis</small></div>
<div class="count tenants"><b>8</b><small><svg width="13" height="13" viewBox="0 0 13 13"><circle cx="6.5" cy="6.5" r="6.5" fill="#fff"/><circle cx="6.5" cy="5" r="2.2" fill="#1c63c4"/><path d="M2.5 10.5a4 3 0 0 1 8 0z" fill="#1c63c4"/></svg>Tenants</small></div>

<div class="area total"><b>422,000.00 Sq.ft.</b><small><svg width="14" height="14" viewBox="0 0 14 14"><circle cx="7" cy="7" r="6" fill="none" stroke="#fff" stroke-width="1.6"/><path d="M4 7l2 2 4-4" stroke="#fff" stroke-width="1.6" fill="none"/></svg>Total Properties Area</small></div>
<div class="area rented"><b>233,500.00 sq.ft</b><small><svg width="14" height="14" viewBox="0 0 14 14"><circle cx="7" cy="7" r="6" fill="none" stroke="#fff" stroke-width="1.6"/><path d="M4 7l2 2 4-4" stroke="#fff" stroke-width="1.6" fill="none"/></svg>Rented Area</small></div>
<div class="area vacant"><b>188,500.00 sq.ft</b><small><svg width="14" height="14" viewBox="0 0 14 14"><circle cx="7" cy="7" r="6" fill="none" stroke="#fff" stroke-width="1.6"/><path d="M4 7l2 2 4-4" stroke="#fff" stroke-width="1.6" fill="none"/></svg>Vacancies Area</small></div>

<section class="chart">
  <svg width="793" height="460" viewBox="0 0 793 460" font-family="Roboto, Arial, sans-serif" font-size="10" fill="#333">
    <g transform="translate(66,20)">
      <rect x="0" y="0" width="101" height="397" fill="var(--col-pink)"/>
      <rect x="101" y="0" width="101" height="397" fill="var(--col-blue)"/>
      <rect x="202" y="0" width="101" height="397" fill="var(--col-pink)"/>
      <rect x="303" y="0" width="101" height="397" fill="var(--col-blue)"/>
      <rect x="404" y="0" width="101" height="397" fill="var(--col-pink)"/>
      <rect x="505" y="0" width="101" height="397" fill="var(--col-blue)"/>
      <rect x="606" y="0" width="101" height="397" fill="var(--col-pink)"/>
      <path d="M335 397V116a11 11 0 0 1 22 0V397z" fill="var(--bar)"/>
      <g stroke="var(--grid)" stroke-width=".6">
        <line x1="0" y1="32" x2="713" y2="32"/>
        <line x1="0" y1="105" x2="713" y2="105"/>
        <line x1="0" y1="178" x2="713" y2="178"/>
        <line x1="0" y1="251" x2="713" y2="251"/>
        <line x1="0" y1="324" x2="713" y2="324"/>
        <line x1="0" y1="397" x2="713" y2="397"/>
        <line x1="0" y1="0" x2="0" y2="397"/>
      </g>
    </g>
    <g text-anchor="end">
      <text x="59" y="48">1.25</text>
      <text x="59" y="121">1.00</text>
      <text x="59" y="194">0.75</text>
      <text x="59" y="267">0.50</text>
      <text x="59" y="340">0.25</text>
    </g>
    <text x="34" y="413">0</text>
    <text transform="translate(20,218) rotate(-90)" text-anchor="middle">Number</text>
    <g text-anchor="middle">
      <text x="117" y="441">27/12/2020</text>
      <text x="218" y="441">28/12/2020</text>
      <text x="319" y="441">29/12/2020</text>
      <text x="420" y="441">30/12/2020</text>
      <text x="521" y="441">31/12/2020</text>
      <text x="622" y="441">01/01/2020</text>
      <text x="723" y="441">02/01/2020</text>
    </g>
  </svg>
</section>

<footer class="legend">
  <div class="item" style="left:41px;top:13px"><span class="dot" style="background:#5fa6f8"></span>Scheduled Maintenance</div>
  <div class="item" style="left:243px;top:13px"><span class="dot" style="background:#7fe37f"></span>Completed Scheduled Maintenance</div>
  <div class="item" style="left:527px;top:13px"><span class="dot" style="background:#f0a068"></span>Future Scheduled Maintenance</div>
  <div class="item" style="left:796px;top:13px"><span class="dot" style="background:#444"></span>Scheduled Work Orders</div>
  <div class="item" style="left:41px;top:44px"><span class="dot" style="background:#8a84d8"></span>Completed Work Orders</div>
  <div class="item" style="left:243px;top:44px"><span class="dot" style="background:#ef4a72"></span>Property Inspections in Progress</div>
  <div class="item" style="left:527px;top:44px"><span class="dot" style="background:#e2cc48"></span>Completed Property Inspections</div>
</footer>

<nav class="sidebar">
  <ul class="nav">
    <li class="active"><svg viewBox="0 0 16 16"><path d="M8 1 1 8h2v7h4v-4h2v4h4V8h2z"/></svg><span>Dashboard</span></li>
    <li><svg viewBox="0 0 16 16"><circle cx="5" cy="5" r="3"/><circle cx="11" cy="5" r="3"/><path d="M0 14a5 4 0 0 1 10 0zM8 14a4 4 0 0 1 8 0z"/></svg><span>Customers</span></li>
    <li><svg viewBox="0 0 16 16"><path d="M8 1 0 8h2v7h12V8h2z"/></svg><span>Properties</span></li>
    <li><svg viewBox="0 0 16 16"><circle cx="8" cy="8" r="7.5"/><circle cx="8" cy="6.5" r="2.5" fill="#2438c4"/><path d="M3.5 12.5a4.5 3.5 0 0 1 9 0z" fill="#2438c4"/></svg><span>Tenants</span></li>
    <li><svg viewBox="0 0 16 16"><circle cx="8" cy="5" r="4.5"/><rect x="3" y="10" width="10" height="6" rx="2"/></svg><span>Contacts</span></li>
    <li><svg viewBox="0 0 16 16"><circle cx="5.5" cy="5.5" r="4.5"/><circle cx="12" cy="12" r="3.5"/><circle cx="5.5" cy="5.5" r="1.6" fill="#2438c4"/></svg><span>Contractors</span></li>
    <li><svg viewBox="0 0 16 16"><circle cx="8" cy="4" r="2.5"/><circle cx="3" cy="6" r="2"/><circle cx="13" cy="6" r="2"/><path d="M3 14a5 5 0 0 1 10 0zM0 12a3 3 0 0 1 5-2.5L4 12zM16 12a3 3 0 0 0-5-2.5l1 2.5z"/></svg><span>Employees</span></li>
    <li><svg viewBox="0 0 16 16"><rect x="1" y="2" width="14" height="12" rx="1"/><g fill="#2438c4"><rect x="3" y="5" width="10" height="1.4"/><rect x="3" y="8" width="10" height="1.4"/><rect x="3" y="11" width="6" height="1.4"/></g></svg><span>Prevents,Maintenance</span></li>
    <li><svg viewBox="0 0 16 16"><circle cx="7" cy="7" r="6"/><circle cx="7" cy="7" r="2.2" fill="#2438c4"/><circle cx="13" cy="13" r="3"/></svg><span>Work Orders</span></li>
    <li><svg viewBox="0 0 16 16"><path d="M3 5h10l-1 10H4z"/><path d="M5.5 5a2.5 2.5 0 0 1 5 0" fill="none" stroke="#fff" stroke-width="1.4"/></svg><span>Purchase Orders</span></li>
    <li><svg viewBox="0 0 16 16"><rect x="1" y="1" width="9" height="14"/><circle cx="10" cy="10" r="3.5" fill="#2438c4" stroke="#fff" stroke-width="1.5"/><path d="M12.5 12.5 15.5 15.5" stroke="#fff" stroke-width="1.6"/></svg><span>Proerties Inspections</span></li>
    <li><svg viewBox="0 0 16 16"><rect x="1" y="7" width="3" height="7"/><rect x="5" y="3" width="3" height="11"/><rect x="9" y="6" width="3" height="8"/><rect x="13" y="9" width="2.5" height="5"/><rect x="0" y="14.5" width="16" height="1.5"/></svg><span>Energy Management</span></li>
    <li><svg viewBox="0 0 16 16"><path d="M8 1 15.5 15H.5z"/><rect x="7.2" y="6" width="1.6" height="5" fill="#2438c4"/><rect x="7.2" y="12" width="1.6" height="1.6" fill="#2438c4"/></svg><span>Risk Mangement</span></li>
    <li><svg viewBox="0 0 16 16"><rect x="0" y="2" width="2.5" height="2.5"/><rect x="4" y="2" width="12" height="2.5"/><rect x="0" y="7" width="2.5" height="2.5"/><rect x="4" y="7" width="12" height="2.5"/><rect x="0" y="12" width="2.5" height="2.5"/><rect x="4" y="12" width="12" height="2.5"/></svg><span>Project Management</span></li>
    <li><svg viewBox="0 0 16 16"><circle cx="9" cy="7" r="6.5"/><circle cx="6.5" cy="9.5" r="5.5" fill="#2438c4" stroke="#fff" stroke-width="1.5"/></svg><span>Finacial-Budgeting</span></li>
    <li><svg viewBox="0 0 16 16"><path d="M1 2h14v10H6l-4 3v-3H1z"/><g fill="#2438c4"><circle cx="5" cy="7" r="1.1"/><circle cx="8" cy="7" r="1.1"/><circle cx="11" cy="7" r="1.1"/></g></svg><span>Tenants Requests</span></li>
    <li><svg viewBox="0 0 16 16"><rect x="2" y="1" width="12" height="14" rx="1"/><g fill="#2438c4"><rect x="4" y="4" width="3" height="2"/><rect x="8" y="4" width="4" height="2"/><rect x="4" y="9" width="3" height="2"/><rect x="8" y="9" width="4" height="2"/></g></svg><span>Repors</span></li>
    <li><svg viewBox="0 0 16 16"><path d="M0 12 5 6l4 3 6-7v2L9 11 5 8l-5 6z"/><rect x="0" y="14.5" width="16" height="1.5"/></svg><span>Visual Reports</span></li>
    <li><svg viewBox="0 0 16 16"><rect x="0" y="4" width="12" height="11" rx="1"/><path d="M3 1h12v11h-2V3H3z"/></svg><span>Files</span></li>
    <li><svg viewBox="0 0 16 16"><path d="M2 0h8l4 4v12H2z"/><g fill="#2438c4"><rect x="4" y="7" width="8" height="1.3"/><rect x="4" y="10" width="8" height="1.3"/></g></svg><span>pages</span></li>
    <li><svg viewBox="0 0 16 16"><circle cx="6" cy="10" r="5"/><circle cx="6" cy="10" r="1.8" fill="#2438c4"/><circle cx="13" cy="3" r="2.8"/></svg><span>Configurations</span></li>
    <li><svg viewBox="0 0 16 16"><path d="M2 2 14 14M14 2 2 14" stroke="#fff" stroke-width="2.4"/><circle cx="3" cy="13" r="2.6"/><circle cx="13" cy="3" r="2.6"/></svg><span>Settings</span></li>
  </ul>
</nav>
</body>
</html>
```